Business card design for my company.
I would like the card's background colour to be black. You can also see our web site to get an idea of our brand. https://www.tmwhomecrafting.com.au/
- Name
- Email

```html
<!DOCTYPE html>
<html lang="en">
<head>
<meta charset="utf-8">
<title>TMW Home Crafting – Business Card</title>
<link href="https://fonts.googleapis.com/css2?family=Poppins:wght@400;600;700&display=swap" rel="stylesheet">
<style>
  :root {
    --stage: #2b2b2b;
    --card: #161616;
    --brand-green: #0f9a48;
    --text-light: #f2f2f2;
    --text-muted: #d9d9d9;
    --edge-white: #ffffff;
  }
  * { box-sizing: border-box; margin: 0; padding: 0; }
  html, body {
    width: 1200px; height: 875px; overflow: hidden;
    background: var(--stage);
    font-family: "Poppins", sans-serif;
  }
  .canvas { position: relative; width: 1200px; height: 875px; }

  .card {
    position: absolute;
    width: 520px; height: 300px;
    background: var(--card);
    border-radius: 18px;
    overflow: hidden;
    box-shadow: 0 20px 40px rgba(0,0,0,.45);
  }
  .card--front { left: 60px; top: 90px; }
  .card--back  { left: 620px; top: 485px; }

  .card__edge {
    position: absolute; left: 0; right: 0; bottom: 0;
    height: 7px; background: var(--brand-green);
  }

  .wordmark {
    display: flex; align-items: center; gap: 12px;
    color: var(--text-light);
    font-weight: 700;
    letter-spacing: 0.04em;
    text-transform: uppercase;
    line-height: 1;
  }
  .wordmark__square { background: var(--brand-green); flex: none; }

  .card--front .wordmark {
    position: absolute; left: 0; right: 0; top: 0; bottom: 7px;
    justify-content: center; font-size: 34px;
  }
  .card--front .wordmark__square { width: 22px; height: 22px; }

  .card--back .wordmark {
    position: absolute; right: 30px; top: 38px; font-size: 20px;
  }
  .card--back .wordmark__square { width: 14px; height: 14px; }

  .card__rule {
    position: absolute; left: 28px; right: 30px; top: 150px;
    height: 1px; background: var(--brand-green); opacity: .6;
  }

  .address {
    position: absolute; right: 30px; top: 112px;
    text-align: right; font-size: 11px; color: var(--text-muted); line-height: 1.4;
  }

  .person { position: absolute; left: 28px; top: 166px; }
  .person__name { color: var(--brand-green); font-weight: 600; font-size: 22px; line-height: 1.1; }
  .person__role { color: var(--text-light); font-size: 11px; margin-top: 2px; }
  .person__divider { width: 150px; height: 1px; background: #4a4a4a; margin: 8px 0 7px; }

  .contact-list { list-style: none; }
  .contact-list li {
    display: flex; align-items: center; gap: 8px;
    color: var(--text-light); font-size: 10.5px; line-height: 1.65;
  }
  .contact-list svg { width: 10px; height: 10px; fill: var(--brand-green); flex: none; }

  .card--back .card__edge { right: 70px; }
  .card__edge-accent {
    position: absolute; right: 0; bottom: 0; width: 70px; height: 7px;
    background: var(--edge-white);
  }
</style>
</head>
<body>
<main class="canvas">

  <section class="card card--front" aria-label="Business card front">
    <div class="wordmark"><span class="wordmark__square"></span>TMW Home Crafting</div>
    <div class="card__edge"></div>
  </section>

  <section class="card card--back" aria-label="Business card back">
    <div class="wordmark"><span class="wordmark__square"></span>TMW Home Crafting</div>
    <p class="address">Rivermead, Eastport, NV<br>Northvale Region</p>
    <div class="card__rule"></div>

    <div class="person">
      <p class="person__name">Daniel Hartley</p>
      <p class="person__role">CEO &amp; Founder</p>
      <div class="person__divider"></div>
      <ul class="contact-list">
        <li>
          <svg viewBox="0 0 24 24" aria-hidden="true"><path d="M6.6 10.8a15.1 15.1 0 0 0 6.6 6.6l2.2-2.2a1 1 0 0 1 1-.25 11.4 11.4 0 0 0 3.6.57 1 1 0 0 1 1 1V20a1 1 0 0 1-1 1A17 17 0 0 1 3 4a1 1 0 0 1 1-1h3.5a1 1 0 0 1 1 1c0 1.25.2 2.45.57 3.57a1 1 0 0 1-.25 1z"/></svg>
          0400 123 456
        </li>
        <li>
          <svg viewBox="0 0 24 24" aria-hidden="true"><path d="M2 5h20v14H2zM4 7v.5l8 5 8-5V7l-8 5z"/></svg>
          info@tmwhomecrafting.com.au
        </li>
        <li>
          <svg viewBox="0 0 24 24" aria-hidden="true"><circle cx="12" cy="12" r="10"/></svg>
          www.tmwhomecrafting.com.au
        </li>
      </ul>
    </div>

    <div class="card__edge"></div>
    <div class="card__edge-accent"></div>
  </section>

</main>
</body>
</html>
```